Business Card for my New Brokerage

Looking to get a business card design for my new Real Estate Brokerage.
I want it with Picture, Phone Number, Email, Website, Office Address
Name and Designation. Please add logo too.

Target Market(s)

Real Estate Investors or Home Buyers

Industry/Entity Type

Real Estate

Contact Information for Business Card

Name, Email, Phone Number, website, email, office address

Colors
EB3D1F
EC4F4E
F09395
F8D3D4
FCEDEE

Requirements
Must have
• Minimalistic, Clean, Modern, Photo
Nice to have
• White and Red Colors

```html
<!DOCTYPE html>
<html lang="en">
<head>
<meta charset="utf-8">
<title>Lumen Realty Inc – Business Card</title>
<link href="https://fonts.googleapis.com/css2?family=Montserrat:wght@500;700;800&family=Jost:wght@400;500&display=swap" rel="stylesheet">
<style>
  :root {
    --page: #dcdcdc;
    --card: #2a2a2a;
    --red: #e00a0a;
    --edge: #eb3d1f;
    --gold: #d4b056;
    --gold-light: #f3e08f;
    --gold-dark: #b88f2e;
    --ink: #f2f2f2;
  }
  * { box-sizing: border-box; margin: 0; padding: 0; }
  html, body { width: 1200px; height: 800px; overflow: hidden; }
  body {
    background: var(--page);
    font-family: "Jost", "Helvetica Neue", Arial, sans-serif;
    position: relative;
  }
  .card {
    position: absolute;
    width: 540px;
    height: 310px;
    background: var(--card);
    border-bottom: 3px solid var(--edge);
    border-left: 2px solid var(--edge);
    overflow: hidden;
    box-shadow: 0 12px 28px rgba(0,0,0,0.22);
  }
  .card--front { left: 40px; top: 245px; }
  .card--back  { left: 620px; top: 245px; }

  .accent-mark {
    position: absolute;
    right: -60px;
    top: -40px;
    width: 300px;
    height: 300px;
    border-radius: 50%;
    background: linear-gradient(135deg, var(--gold-dark), var(--gold-light) 50%, var(--gold-dark));
  }

  .details {
    position: absolute;
    left: 34px;
    top: 34px;
  }
  .brand-name {
    font-family: "Montserrat", Arial, sans-serif;
    font-weight: 700;
    color: var(--red);
    font-size: 22px;
    letter-spacing: 1px;
    text-transform: uppercase;
  }
  .person {
    margin-top: 34px;
    font-family: "Montserrat", Arial, sans-serif;
    font-weight: 800;
    color: var(--gold);
    font-size: 19px;
    text-transform: uppercase;
    letter-spacing: 0.3px;
  }
  .role {
    color: var(--ink);
    font-size: 14px;
    margin-top: 2px;
  }
  .address {
    color: var(--ink);
    font-size: 13.5px;
    line-height: 1.35;
    margin-top: 16px;
    font-style: normal;
  }
  .contacts {
    list-style: none;
    margin-top: 14px;
  }
  .contacts li {
    display: flex;
    align-items: center;
    gap: 9px;
    color: var(--ink);
    font-size: 13.5px;
    line-height: 1.45;
  }
  .contacts svg { width: 12px; height: 12px; flex: none; }

  .brand-center {
    position: absolute;
    inset: 0;
    display: flex;
    align-items: center;
    justify-content: center;
  }
  .brand-center .brand-name { font-size: 38px; letter-spacing: 2px; }
</style>
</head>
<body>

<section class="card card--front" aria-label="Business card front">
  <div class="accent-mark" aria-hidden="true"></div>
  <div class="details">
    <p class="brand-name">Lumen Realty Inc</p>
    <h1 class="person">Daniel Brooks</h1>
    <p class="role">Founder &amp; CEO</p>
    <address class="address">4120 Willow Crest Drive<br>Juneau, Alaska 34512</address>
    <ul class="contacts">
      <li>
        <svg viewBox="0 0 12 12" aria-hidden="true"><path d="M2 1 L4.5 1 L5.3 3.5 L4 4.6 Q5 7 7.4 8 L8.5 6.7 L11 7.5 L11 10 Q6 11 3 8 Q0.5 5 2 1 Z" fill="var(--gold)"/></svg>
        907-512-4480
      </li>
      <li>
        <svg viewBox="0 0 12 12" aria-hidden="true"><rect x="3" y="0.5" width="6" height="11" rx="1" fill="none" stroke="var(--gold)" stroke-width="1.3"/><circle cx="6" cy="9.5" r="0.7" fill="var(--gold)"/></svg>
        907-618-2297
      </li>
      <li>
        <svg viewBox="0 0 12 12" aria-hidden="true"><rect x="0.7" y="2" width="10.6" height="8" fill="none" stroke="var(--gold)" stroke-width="1.3"/><path d="M1 2.5 L6 6.5 L11 2.5" fill="none" stroke="var(--gold)" stroke-width="1.3"/></svg>
        hello@lumenrealty.com
      </li>
      <li>
        <svg viewBox="0 0 12 12" aria-hidden="true"><circle cx="6" cy="6" r="5.2" fill="none" stroke="var(--gold)" stroke-width="1.2"/><ellipse cx="6" cy="6" rx="2.2" ry="5.2" fill="none" stroke="var(--gold)" stroke-width="1"/><path d="M1 6 H11" stroke="var(--gold)" stroke-width="1"/></svg>
        www.lumenrealty.com
      </li>
    </ul>
  </div>
</section>

<section class="card card--back" aria-label="Business card back">
  <div class="brand-center">
    <p class="brand-name">Lumen Realty Inc</p>
  </div>
</section>

</body>
</html>
```